Direct Mail Letter / Reply Device / Outer Envelope

I'm interested in seeing if I can give my charity's annual appeal a fresh look and feel. I have written the letter though edits might be needed. We're really looking for 'pop'. Edits to the letter will need to happen before our final design. My budget for design is about $250.00 but I may be able to negotiate for the right design.

Target Market(s)

Donors to a specific charity

Font styles to use
Serif
Sans Serif

Colors

Designer to choose colors to be used in the design.

Requirements
Must have
• Color photos that make the most of the photos I have regardless of resolutions. I need something in a format that will let me make edits and / or reuse next year or for my thank you letter. Basically, a Word friendly version.

```html
<!DOCTYPE html>
<html lang="en">
<head>
<meta charset="utf-8">
<title>Retriever Haven – Annual Appeal Letter, Page 2</title>
<link rel="stylesheet" href="https://fonts.googleapis.com/css2?family=Work+Sans:wght@300;400;700&family=Gochi+Hand&display=swap">
<style>
  :root {
    --teal-deep: #1d8fa3;
    --teal-mid: #2a9fb3;
    --teal-bright: #0aa0c7;
    --teal-soft: #3aaabd;
    --ink: #2b2b2b;
    --ink-strong: #0d0d0d;
    --muted: #8a8f92;
    --rule: #7a9aa3;
    --ghost: #e6efee;
    --paper: #ffffff;
  }
  html, body {
    margin: 0;
    padding: 0;
    overflow: hidden;
    background: var(--paper);
  }
  .page {
    position: relative;
    width: 849px;
    height: 1200px;
    overflow: hidden;
    background: var(--paper);
    font-family: "Work Sans", Arial, sans-serif;
  }
  .header-band,
  .ghost-mark {
    position: absolute;
    left: 0;
    top: 0;
  }
  .feature-photo {
    position: absolute;
    left: 95px;
    top: 56px;
    width: 256px;
    height: 256px;
    border-radius: 50%;
    background: var(--paper);
    padding: 0;
  }
  .feature-photo .photo-fill {
    position: absolute;
    inset: 6px;
    border-radius: 50%;
    background:
      radial-gradient(circle at 55% 30%, #d8d2c4 0 18%, transparent 34%),
      linear-gradient(180deg, #8fb36a 0%, #6e9b45 55%, #5d8a3a 100%);
  }
  .photo-caption {
    position: absolute;
    left: 412px;
    top: 100px;
    margin: 0;
    font-family: "Gochi Hand", cursive;
    font-size: 40px;
    font-weight: 400;
    color: #eaf6f8;
    letter-spacing: 1px;
  }
  .letter-body {
    position: absolute;
    left: 154px;
    top: 379px;
    width: 545px;
    font-size: 15.2px;
    line-height: 24.9px;
    font-weight: 300;
    color: var(--ink);
  }
  .letter-body p {
    margin: 0 0 8.5px;
  }
  .letter-body .appeal {
    font-weight: 700;
    color: var(--ink-strong);
  }
  .letter-footer {
    position: absolute;
    left: 154px;
    top: 1082px;
    width: 541px;
    border-top: 1px solid var(--rule);
    text-align: center;
    color: var(--muted);
    font-size: 13.4px;
    font-weight: 300;
  }
  .letter-footer .contact {
    margin: 11px 0 0;
  }
  .letter-footer .web {
    margin: 5px 0 0;
    font-weight: 700;
    color: #555a5d;
  }
</style>
</head>
<body>
<div class="page">

  <svg class="ghost-mark" width="849" height="1200" viewBox="0 0 849 1200" role="img" aria-label="Large faint decorative silhouette of a sitting Labrador behind the letter text">
    <defs>
      <linearGradient id="ghostFade" x1="0" y1="0" x2="0" y2="1">
        <stop offset="0" stop-color="#e6efee" stop-opacity="0.7"/>
        <stop offset="1" stop-color="#e2ecea" stop-opacity="1"/>
      </linearGradient>
    </defs>
    <path d="M0 780 C120 700 230 640 300 600 C330 700 360 760 420 820 C470 900 470 1000 430 1060 L420 1200 L0 1200 Z" fill="url(#ghostFade)"/>
  </svg>

  <svg class="header-band" width="849" height="320" viewBox="0 0 849 320" aria-hidden="true">
    <defs>
      <linearGradient id="bandMain" x1="0" y1="0" x2="1" y2="1">
        <stop offset="0" stop-color="#0b9fc6"/>
        <stop offset="0.5" stop-color="#1e93aa"/>
        <stop offset="1" stop-color="#1f8fa2"/>
      </linearGradient>
    </defs>
    <polygon points="0,0 849,0 849,300 352,176 104,144 0,172" fill="url(#bandMain)"/>
    <polygon points="0,0 300,0 0,100" fill="#0aa4cc" opacity="0.55"/>
    <polygon points="520,0 849,0 849,210" fill="#3aaabd" opacity="0.5"/>
    <polygon points="0,90 260,160 104,144 0,172" fill="#2a9fb3" opacity="0.6"/>
  </svg>

  <div class="feature-photo">
    <div class="photo-fill" role="img" aria-label="Photo of Ramsey, a black Lab in a blue mobility wheelchair, meeting a spotted pony across a wire fence on green grass"></div>
  </div>

  <svg class="header-band" width="849" height="320" viewBox="0 0 849 320" aria-hidden="true">
    <path d="M418 94 C380 84 340 110 322 162" fill="none" stroke="#e8f3f5" stroke-width="3" stroke-linecap="round"/>
    <path d="M312 142 L322 164 L338 148" fill="none" stroke="#e8f3f5" stroke-width="3" stroke-linecap="round" stroke-linejoin="round"/>
  </svg>

  <p class="photo-caption">'Ramsey'</p>

  <div class="letter-body">
    <p>worked daily to connect with shelters and rescue workers who were on the ground. Initially, their need was to establish temporary shelters; row upon row in any kind of warehouse they could find.</p>
    <p>Then, Retriever Haven got involved. We committed to taking every Lab identified as needing a new home.&nbsp; Our first transport took 3 days to reach us and had 25 Labs (one was a last-minute surprise addition: “Stowaway”). Many didn’t even have names so we named them. Another transport arrived a week later with one more dog who was too ill to travel initially.</p>
    <p>As I write this letter, I can share the story of Retriever Haven's latest survivor! Hurricane Irma hit Turks &amp; Caicos as a Category 5 storm destroying so much, including the animal shelter.&nbsp; A local rescue partnered with the shelter and arranged for 16 dogs to be transported to our area. Crunch, a 3 year old black Lab</p>
    <p>Your donations mean that we can spend the extra funds on transporting young, healthy Labs for whom families in our service area anxiously await. We can meet the dramatically increasing need for heartworm treatment created by the many dogs from farther and farther south in North Carolina. That means hundreds of dollars for each dog we save from the certain painful death of heartworm and restore to good health.</p>
    <p class="appeal">My request to you for this year is simple. Please donate now to make sure that we can continue to be the organization that can be there for every Lab that needs us.</p>
    <p>Right now, we are in the process of helping another special Lab. Too many of us have lost our Labs to cancer and we know that treatments</p>
  </div>

  <footer class="letter-footer">
    <p class="contact">Lab Line: (301) 555-0142&nbsp; | P.O. Box 4720 Fairbrook VA 22090</p>
    <p class="web">www.retrieverhaven.org</p>
  </footer>

</div>
</body>
</html>
```